Corvel Capital LLC

Need Professional Business cards for New Investment Fund

Target Market(s)

High Quality investors

Industry/Entity Type

Financial

Contact Information for Business Card

Phone Number +1 555 284 6190
Name Lukas Varenko
Title Fund Manager
email lv@FundCorvel.com
Website www.FundCorvel.com

Colors

Designer to choose colors to be used in the design.

Requirements
Must have
• Must have our Logo and all of the above. Must be made so lettering and loge can be raised

```html
<!DOCTYPE html>
<html lang="en">
<head>
<meta charset="utf-8">
<title>Kestro – Business Card</title>
<link href="https://fonts.googleapis.com/css2?family=Mulish:wght@700&family=Lato:wght@400;700&display=swap" rel="stylesheet">
<style>
  :root {
    --backdrop: #bdbdbd;
    --card-dark: #414b3f;
    --brand-green: #22e600;
    --paper: #ffffff;
    --text-light: #f2f2f2;
    --shadow: rgba(0,0,0,0.35);
  }
  * { margin: 0; padding: 0; box-sizing: border-box; }
  html, body {
    width: 1200px; height: 802px; overflow: hidden;
    background: var(--backdrop);
  }
  .canvas { position: relative; width: 1200px; height: 802px; }
  .card {
    position: absolute; top: 274px; width: 443px; height: 265px;
    box-shadow: 2px 3px 6px var(--shadow); overflow: hidden;
  }
  .card--front { left: 136px; background: var(--paper); }
  .card--back { left: 625px; background: var(--card-dark); }

  .front__info {
    position: absolute; left: 0; top: 0; width: 211px; height: 100%;
    background: var(--card-dark);
  }
  .front__stripe {
    position: absolute; left: 211px; top: 0; width: 4px; height: 100%;
    background: var(--brand-green);
  }
  .holder__name {
    position: absolute; left: 24px; top: 74px;
    font-family: "Mulish", sans-serif; font-weight: 700;
    font-size: 15px; letter-spacing: 0.2px; color: var(--brand-green);
    white-space: nowrap;
  }
  .holder__title {
    position: absolute; left: 24px; top: 92px;
    font-family: "Lato", sans-serif; font-size: 12.5px; color: var(--text-light);
  }
  .contact {
    position: absolute; left: 24px; top: 142px; list-style: none;
    font-family: "Lato", sans-serif; font-size: 12.5px; color: var(--text-light);
  }
  .contact__item { display: flex; align-items: center; height: 16px; white-space: nowrap; }
  .contact__icon { width: 10px; height: 10px; margin-right: 5px; fill: var(--brand-green); }

  .front__brand {
    position: absolute; left: 215px; top: 0; right: 0; height: 100%;
    display: flex; align-items: center; justify-content: center; gap: 8px;
  }
  .brand__mark { width: 14px; height: 14px; background: var(--brand-green); }
  .brand__name {
    font-family: "Lato", sans-serif; font-weight: 700; font-size: 26px;
    letter-spacing: 2px; color: var(--card-dark);
  }

  .back__panel {
    position: absolute; left: 0; top: 0; width: 205px; height: 100%;
    background: var(--brand-green);
  }
  .back__brand {
    position: absolute; left: 222px; top: 0; height: 100%;
    display: flex; align-items: center;
    font-family: "Lato", sans-serif; font-weight: 700; font-size: 30px;
    letter-spacing: 3px; color: var(--text-light);
  }
</style>
</head>
<body>
<main class="canvas">
  <section class="card card--front">
    <div class="front__info">
      <p class="holder__name">LUKAS VARENKO</p>
      <p class="holder__title">Fund Manager</p>
      <ul class="contact">
        <li class="contact__item">
          <svg class="contact__icon" viewBox="0 0 10 10"><path d="M1 4 Q5 0 9 4 L8 5 L6.5 4 L6.5 3.2 Q5 2.8 3.5 3.2 L3.5 4 L2 5 Z"/><rect x="2.5" y="5" width="5" height="4" rx="0.6"/></svg>
          +1 555 284 6190
        </li>
        <li class="contact__item">
          <svg class="contact__icon" viewBox="0 0 10 10"><path d="M0.5 2 H9.5 V8 H0.5 Z M1 2.5 L5 5.5 L9 2.5" stroke="#414b3f" stroke-width="0.7"/></svg>
          lv@FundCorvel.com
        </li>
        <li class="contact__item">
          <svg class="contact__icon" viewBox="0 0 10 10"><circle cx="5" cy="5" r="4.5"/><path d="M3 3 Q5 4 4 6 M6 2 Q7 5 6.5 8" stroke="#414b3f" stroke-width="0.8" fill="none"/></svg>
          www.FundCorvel.com
        </li>
      </ul>
    </div>
    <div class="front__stripe"></div>
    <div class="front__brand">
      <span class="brand__mark"></span>
      <span class="brand__name">KESTRO</span>
    </div>
  </section>

  <section class="card card--back">
    <div class="back__panel"></div>
    <div class="back__brand">KESTRO</div>
  </section>
</main>
</body>
</html>
```